New Zealand Marlborough Sauvignon Blanc wine packaging design

We need packaging design for our new wine brand, Dunmore Vale. The wine is a New Zealand Marlborough Sauvignon Blanc. We would like the packaging will portray elegance and style with an understated label. We are looking for a label that portrays the elegance of the French Riviera. The label should be round or pill shaped.
Updates

Industry/Entity Type

Wine

Font styles to use
Serif
Sans Serif

Requirements
Must have
• The words in order of importance: Dunmore Vale, Sauvignon Blanc, Marlborough, New Zealand. It should be fit to the bottle posted in the links
Nice to have
• a pill shape or circular shape
Should not have
• Illustrations of wine bottles, wine glasses, or grapes

```html
<!DOCTYPE html>
<html lang="en">
<head>
<meta charset="utf-8">
<title>Dunmore Vale Sauvignon Blanc Label</title>
<link rel="stylesheet" href="https://fonts.googleapis.com/css2?family=Poppins:wght@600&family=Cormorant+Garamond:wght@500;600&display=swap">
<style>
  :root {
    --backdrop: #eceff3;
    --label-dark: #2b2b2d;
    --label-mid: #3a3a3c;
    --rim-gold: #d6dc7a;
    --rim-deep: #7f8a2c;
    --accent-green: #a9bb3e;
    --brand-grey: #6d6d70;
    --type-dark: #161617;
  }
  * { margin: 0; padding: 0; box-sizing: border-box; }
  html, body {
    width: 1200px;
    height: 1200px;
    overflow: hidden;
    background: var(--backdrop);
  }
  .canvas {
    position: relative;
    width: 1200px;
    height: 1200px;
    display: flex;
    align-items: center;
    justify-content: center;
  }
  .label {
    position: relative;
    width: 560px;
    height: 900px;
    border-radius: 280px;
    padding: 10px;
    background: linear-gradient(160deg, var(--rim-gold), var(--rim-deep) 55%, var(--rim-gold));
  }
  .label-face {
    width: 100%;
    height: 100%;
    border-radius: 270px;
    background: radial-gradient(ellipse at 50% 35%, var(--label-mid), var(--label-dark) 75%);
    display: flex;
    flex-direction: column;
    align-items: center;
    padding-top: 70px;
  }
  .crest {
    width: 90px;
    height: 100px;
    border-radius: 8px;
    background: linear-gradient(180deg, #b8c94c, var(--accent-green));
  }
  .brand-name {
    margin-top: 60px;
    font-family: "Poppins", sans-serif;
    font-weight: 600;
    font-size: 92px;
    line-height: 0.92;
    letter-spacing: -2px;
    text-align: center;
    color: var(--brand-grey);
  }
  .estate-scene {
    margin-top: 60px;
    width: 200px;
    height: 150px;
    border-radius: 6px;
    background: linear-gradient(180deg, #9fb03a, #7f9128);
  }
  .varietal {
    margin-top: 62px;
    font-family: "Cormorant Garamond", serif;
    font-weight: 600;
    font-size: 40px;
    letter-spacing: 1px;
    color: var(--type-dark);
  }
  .vintage {
    font-family: "Cormorant Garamond", serif;
    font-weight: 600;
    font-size: 32px;
    color: var(--type-dark);
    line-height: 1;
  }
  .region {
    margin-top: 34px;
    font-family: "Cormorant Garamond", serif;
    font-weight: 600;
    font-size: 30px;
    color: var(--type-dark);
    line-height: 1;
  }
  .country {
    margin-top: 4px;
    font-family: "Cormorant Garamond", serif;
    font-weight: 500;
    font-size: 15px;
    letter-spacing: 1px;
    color: var(--type-dark);
  }
</style>
</head>
<body>
  <main class="canvas">
    <section class="label">
      <div class="label-face">
        <div class="crest" role="img" aria-label="Fleur-de-lis crest ornament"></div>
        <h1 class="brand-name">Dunmore<br>Vale</h1>
        <div class="estate-scene" role="img" aria-label="Illustration of a chateau above rolling vineyard rows"></div>
        <p class="varietal">SAUVIGNON BLANC</p>
        <p class="vintage">2023</p>
        <p class="region">MARLBOROUGH</p>
        <p class="country">NEW ZEALAND</p>
      </div>
    </section>
  </main>
</body>
</html>
```